Business Card Design for Property Development Company Director

I am looking for a professional and unforgettable business card design for our Director of our Property Development Company.
Please see attached .pptx file to find out what information to include. You don't have to follow the exact format shown in the file - I am interested to see your creative flair using the information provided.

```html
<!DOCTYPE html>
<html lang="en">
<head>
<meta charset="utf-8">
<title>Harwell Property Group – Business Card</title>
<link href="https://fonts.googleapis.com/css2?family=Roboto:wght@400;500;700&family=Roboto+Condensed:wght@700&display=swap" rel="stylesheet">
<style>
  :root {
    --backdrop: #e4e5e7;
    --card: #f4f4f4;
    --brand-blue: #1f3f8c;
    --brand-grey: #56585c;
    --text-grey: #5e6064;
    --white: #ffffff;
  }
  * { box-sizing: border-box; margin: 0; padding: 0; }
  html, body { width: 1200px; height: 726px; overflow: hidden; }
  body {
    background: var(--backdrop);
    font-family: "Roboto", Arial, sans-serif;
    position: relative;
  }
  .card {
    position: absolute;
    width: 540px;
    height: 309px;
    background: var(--card);
    box-shadow: 0 6px 18px rgba(0,0,0,0.12);
    overflow: hidden;
  }
  .card--front { left: 40px; top: 200px; }
  .card--back { left: 620px; top: 208px; }

  /* Front */
  .tagline {
    position: absolute; top: 36px; left: 0; right: 0;
    text-align: center;
    color: var(--brand-blue);
    font-size: 18px; line-height: 22px; font-weight: 400;
  }
  .brand {
    position: absolute; top: 118px; left: 0; right: 0;
    display: flex; align-items: center; justify-content: center; gap: 16px;
  }
  .brand__square {
    width: 46px; height: 46px; background: var(--brand-grey);
  }
  .brand__name {
    color: var(--brand-blue);
    font-weight: 700; font-size: 34px; line-height: 1.05;
    letter-spacing: 1px; text-transform: uppercase;
  }
  .brand__name span { display: block; font-size: 17px; letter-spacing: 5.2px; }
  .invite {
    position: absolute; top: 232px; left: 0; right: 0;
    text-align: center; font-size: 14px; color: var(--text-grey);
  }
  .invite strong { color: var(--brand-blue); font-weight: 400; }
  .rule {
    position: absolute; left: 0; right: 0; top: 262px; height: 9px; display: flex;
  }
  .rule__grey { flex: 0 0 46%; background: var(--brand-grey); }
  .rule__blue { flex: 1; background: var(--brand-blue); }

  /* Back */
  .back-shape { position: absolute; inset: 0; }
  .back-brand {
    position: absolute; left: 40px; top: 132px;
    display: flex; align-items: center; gap: 12px;
  }
  .back-brand__square { width: 34px; height: 34px; background: var(--brand-grey); }
  .back-brand__name {
    color: var(--brand-grey); font-weight: 700; font-size: 32px;
    letter-spacing: 1px; text-transform: uppercase;
  }
  .contact {
    position: absolute; left: 388px; top: 58px; width: 145px;
    color: var(--white);
  }
  .contact__name {
    font-family: "Roboto Condensed", Arial, sans-serif;
    font-weight: 700; font-size: 19px;
  }
  .contact__role { font-size: 12px; margin-bottom: 16px; }
  .contact__row {
    display: flex; align-items: center; gap: 7px;
    font-size: 12px; line-height: 18px;
  }
  .contact__row svg { width: 11px; height: 11px; flex: 0 0 11px; }
  .contact__licence { font-size: 12px; line-height: 16px; margin-top: 2px; }
</style>
</head>
<body>

<section class="card card--front" aria-label="Card front">
  <p class="tagline">Property Development<br>&amp; Site Acquisition Specialists</p>
  <div class="brand">
    <div class="brand__square"></div>
    <div class="brand__name">Harwell<span>Property Group</span></div>
  </div>
  <p class="invite">Ask me about our <strong>INVESTMENT &amp; PARTNERSHIP</strong> opportunities</p>
  <div class="rule"><div class="rule__grey"></div><div class="rule__blue"></div></div>
</section>

<section class="card card--back" aria-label="Card back">
  <svg class="back-shape" viewBox="0 0 540 309" width="540" height="309" aria-hidden="true">
    <path d="M262 0 Q392 120 350 309 L540 309 L540 0 Z" fill="var(--brand-grey)"/>
    <path d="M272 0 Q404 120 362 309 L540 309 L540 0 Z" fill="var(--brand-blue)"/>
  </svg>
  <div class="back-brand">
    <div class="back-brand__square"></div>
    <div class="back-brand__name">Harwell</div>
  </div>
  <div class="contact">
    <p class="contact__name">Daniel Mercer</p>
    <p class="contact__role">Director</p>
    <p class="contact__row">
      <svg viewBox="0 0 12 12"><path d="M3 1 L5 3.5 L4 5 Q5 7 7 8 L8.5 7 L11 9 L9.5 11 Q4 10.5 1 3 Z" fill="none" stroke="#fff" stroke-width="1"/></svg>
      0400 123 456
    </p>
    <p class="contact__row">
      <svg viewBox="0 0 12 12"><rect x="1" y="2.5" width="10" height="7" fill="#fff"/><path d="M1 2.5 L6 6.5 L11 2.5" fill="none" stroke="#1f3f8c" stroke-width="1"/></svg>
      daniel@harwell.com.au
    </p>
    <p class="contact__row">
      <svg viewBox="0 0 12 12"><circle cx="6" cy="6" r="5" fill="#fff"/><path d="M1 6 H11 M6 1 Q3 6 6 11 M6 1 Q9 6 6 11" fill="none" stroke="#1f3f8c" stroke-width="0.8"/></svg>
      www.harwell.com.au
    </p>
    <p class="contact__licence">Real Estate Lic:<br>1234567 &amp; 1234568</p>
  </div>
</section>

</body>
</html>
```